Yard sign design for high end luxury home builder.

Need a design for signage on custom homes that are being built. I already have a logo that I am satisfied with that needs to be incorporated. I need the following incorporated in the design of the sign-
- Lic number 381526
- phone number (805) 555-0148‬
- quennbuilderscrew.com
- Logo/Branding

If possible it may be nice to have the following quote that is on are business cards-

Quote from Gerard of Norvelle-
HE WHO WORKS WITH HIS HANDS IS A LABORER.
HE WHO WORKS WITH HIS HANDS & HIS HEAD IS A CRAFTSMAN.
HE WHO WORKS WITH HIS HANDS & HIS HEAD & HIS HEART IS AN ARTISAN.
-GERARD OF NORVELLE

Target Market(s)

Archetect, Designers, Clients desiring to build a new home or remodel.

Colors
fde9d4
fee4d5
fabb94
fac994
faa54b
f68d4d
f37122
f78f20
f68e4e

Requirements
Must have
• - Lic number 381526
• - phone number (805) 555-0148‬
• - quennbuilderscrew.com
• - Logo/Branding
Nice to have
• Quote from Gerard of Norvelle-
• HE WHO WORKS WITH HIS HANDS IS A LABORER.
• HE WHO WORKS WITH HIS HANDS & HIS HEAD IS A CRAFTSMAN.
• HE WHO WORKS WITH HIS HANDS & HIS HEAD & HIS HEART IS AN ARTISAN.
• -GERARD OF NORVELLE
• OR the below statement-
• Craftsmen that Care
Should not have
• Any additional verbiage not specified above including any type of verbiage about what kind of company we are. For instance- Integrity, reputable... It's just all played out. Im just looking for a bitching design that has the info that compliments my logo/branding.

```html
<!DOCTYPE html>
<html lang="en">
<head>
<meta charset="utf-8">
<title>Quenn Builders Crew – Yard Sign</title>
<link rel="stylesheet" href="https://fonts.googleapis.com/css2?family=PT+Serif:wght@400;700&display=swap">
<style>
  :root {
    --page: #ffffff;
    --dark-bg: #1c1a19;
    --tan: #a38d72;
    --light-bg: #eceeed;
    --brown: #4b3424;
  }
  html, body {
    margin: 0;
    padding: 0;
    width: 1200px;
    height: 1200px;
    overflow: hidden;
    background: var(--page);
    font-family: "PT Serif", Georgia, serif;
  }
  .canvas {
    position: relative;
    width: 1200px;
    height: 1200px;
  }
  .sign {
    position: absolute;
    top: 246px;
    width: 523px;
    height: 696px;
    background: var(--bg);
    color: var(--ink);
    box-sizing: border-box;
  }
  .sign--dark { left: 58px; --bg: var(--dark-bg); --ink: var(--tan); --pill-text: var(--dark-bg); }
  .sign--light { left: 611px; --bg: var(--light-bg); --ink: var(--brown); --pill-text: var(--light-bg); }

  .sign__frame {
    position: absolute;
    inset: 8px;
    border: 2px solid var(--ink);
  }
  .sign__tagline {
    position: absolute;
    top: 30px; left: 0; right: 0;
    text-align: center;
    font-size: 46px;
    line-height: 56px;
    margin: 0;
    font-weight: 400;
  }
  .sign__brand {
    position: absolute;
    top: 95px; left: 40px; right: 40px;
    height: 310px;
    display: flex;
    align-items: center;
    justify-content: center;
    text-align: center;
    font-size: 64px;
    line-height: 76px;
    font-weight: 700;
    margin: 0;
  }
  .sign__phone {
    position: absolute;
    top: 432px; left: 0; right: 0;
    text-align: center;
    font-size: 62px;
    line-height: 72px;
    margin: 0;
  }
  .quote {
    position: absolute;
    top: 505px; left: 54px; right: 53px;
    text-align: center;
  }
  .quote__rule {
    display: block;
    width: 100%;
    height: 30px;
  }
  .quote__text {
    margin: 0;
    font-size: 13px;
    line-height: 17px;
  }
  .quote__text strong { font-weight: 700; }
  .quote__divider {
    width: 178px;
    height: 1px;
    background: var(--ink);
    margin: 8px auto 7px;
  }
  .quote__author {
    font-size: 13px;
    line-height: 16px;
    font-weight: 700;
    font-style: normal;
  }
  .sign__url {
    position: absolute;
    top: 648px; left: 100px;
    width: 322px;
    height: 42px;
    background: var(--ink);
    color: var(--pill-text);
    border-radius: 14px 14px 0 0;
    text-align: center;
    font-size: 24px;
    line-height: 42px;
  }
  .sign__license {
    position: absolute;
    top: 667px; left: 433px;
    font-size: 10px;
    font-weight: 700;
  }
</style>
</head>
<body>
<main class="canvas">

  <section class="sign sign--dark">
    <div class="sign__frame"></div>
    <h1 class="sign__tagline">Craftsmen That Care</h1>
    <p class="sign__brand">Quenn Builders Crew</p>
    <p class="sign__phone">(805) 555-0148</p>
    <div class="quote">
      <svg class="quote__rule" viewBox="0 0 416 30" preserveAspectRatio="none" aria-hidden="true">
        <line x1="0" y1="15" x2="190" y2="15" stroke="#a38d72" stroke-width="1"/>
        <line x1="226" y1="15" x2="416" y2="15" stroke="#a38d72" stroke-width="1"/>
        <text x="208" y="27" text-anchor="middle" font-family="PT Serif, serif" font-size="30" font-weight="700" fill="#a38d72">&#8220;</text>
      </svg>
      <p class="quote__text">He who works with his hands is a <strong>laborer</strong>.<br>
        He who works with his hands &amp; his head is a <strong>craftsman</strong>.<br>
        He who works with his hands &amp; his head &amp; his heart is<br>
        an <strong>artisan</strong>.</p>
      <div class="quote__divider"></div>
      <cite class="quote__author">Gerard of Norvelle</cite>
    </div>
    <div class="sign__url">quennbuilderscrew.com</div>
    <div class="sign__license">Lic 381526</div>
  </section>

  <section class="sign sign--light">
    <div class="sign__frame"></div>
    <h1 class="sign__tagline">Craftsmen That Care</h1>
    <p class="sign__brand">Quenn Builders Crew</p>
    <p class="sign__phone">(805) 555-0148</p>
    <div class="quote">
      <svg class="quote__rule" viewBox="0 0 416 30" preserveAspectRatio="none" aria-hidden="true">
        <line x1="0" y1="15" x2="190" y2="15" stroke="#4b3424" stroke-width="1"/>
        <line x1="226" y1="15" x2="416" y2="15" stroke="#4b3424" stroke-width="1"/>
        <text x="208" y="27" text-anchor="middle" font-family="PT Serif, serif" font-size="30" font-weight="700" fill="#4b3424">&#8220;</text>
      </svg>
      <p class="quote__text">He who works with his hands is a <strong>laborer</strong>.<br>
        He who works with his hands &amp; his head is a <strong>craftsman</strong>.<br>
        He who works with his hands &amp; his head &amp; his heart is<br>
        an <strong>artisan</strong>.</p>
      <div class="quote__divider"></div>
      <cite class="quote__author">Gerard of Norvelle</cite>
    </div>
    <div class="sign__url">quennbuilderscrew.com</div>
    <div class="sign__license">Lic 381526</div>
  </section>

</main>
</body>
</html>
```